Stationery and Business Card Design

We need stationary design for our new company lanternfold. Lanternfold is a company that provides city apartment rentals for tourists in Athens We need business cards, letterheads for A4 and A5 and envelopes for A4 A5. The design needs to be modern, friendly and corporate.

Target Market(s)

City Tourists

Industry/Entity Type

Tourism

```html
<!DOCTYPE html>
<html lang="en">
<head>
<meta charset="utf-8">
<title>Lanternfold – Business Card</title>
<link href="https://fonts.googleapis.com/css2?family=Raleway:wght@400;500;600&display=swap" rel="stylesheet">
<style>
  :root {
    --backdrop: #e9e7e4;
    --charcoal: #3b3b3d;
    --charcoal-dark: #2c2c2e;
    --berry: #9b1d5a;
    --ink: #2a2a2a;
    --paper: #ffffff;
    --band-text: #cfcfcf;
    --frame: #f2f2f2;
  }
  * { margin: 0; padding: 0; box-sizing: border-box; }
  html, body {
    width: 1200px; height: 900px; overflow: hidden;
    background: var(--backdrop);
    font-family: "Raleway", Arial, sans-serif;
  }
  .canvas { position: relative; width: 1200px; height: 900px; }

  .card {
    position: absolute; left: 300px;
    width: 600px; height: 343px;
    box-shadow: 0 8px 24px rgba(0,0,0,0.18);
    overflow: hidden;
  }

  /* Front */
  .card--front {
    top: 70px;
    background: linear-gradient(135deg, var(--charcoal) 0%, var(--charcoal-dark) 100%);
  }
  .card--front .frame {
    position: absolute; inset: 16px;
    border: 3px solid var(--frame);
  }
  .card--front .brand {
    position: absolute; left: 0; right: 0; top: 70px;
    display: flex; flex-direction: column; align-items: center; gap: 18px;
  }
  .brand-square {
    width: 86px; height: 76px; background: var(--berry);
  }
  .card--front .brand-name {
    font-size: 62px; font-weight: 500; color: var(--berry); letter-spacing: -0.5px; line-height: 1;
  }

  /* Back */
  .card--back { top: 462px; background: var(--paper); }
  .card--back .tab {
    position: absolute; left: 0; top: 78px;
  }
  .identity { position: absolute; left: 46px; top: 62px; }
  .identity .name {
    font-size: 24px; font-weight: 500; color: var(--berry); letter-spacing: 0.5px;
  }
  .identity .role {
    font-size: 20px; font-weight: 500; color: var(--ink); margin-top: 2px;
  }
  .contacts {
    position: absolute; left: 46px; top: 150px;
    list-style: none; display: flex; flex-direction: column; gap: 12px;
  }
  .contacts li {
    display: flex; align-items: center; gap: 12px;
    font-size: 17px; color: var(--ink); letter-spacing: 0.3px;
  }
  .contacts .icon { width: 24px; height: 24px; flex: none; }

  .card--back .brand {
    position: absolute; right: 58px; top: 70px;
    display: flex; flex-direction: column; align-items: center; gap: 10px;
  }
  .card--back .brand-square { width: 72px; height: 62px; }
  .card--back .brand-name {
    font-size: 42px; font-weight: 500; color: var(--berry); line-height: 1;
  }
  .band {
    position: absolute; left: 0; right: 0; bottom: 0; height: 78px;
    background: var(--charcoal);
    display: flex; align-items: center; justify-content: flex-end; padding-right: 90px;
  }
  .band .web {
    font-size: 18px; color: var(--band-text); letter-spacing: 1.5px;
  }
</style>
</head>
<body>
<main class="canvas">

  <section class="card card--front" aria-label="Business card front">
    <div class="frame"></div>
    <div class="brand">
      <div class="brand-square"></div>
      <div class="brand-name">Lanternfold</div>
    </div>
  </section>

  <section class="card card--back" aria-label="Business card back">
    <svg class="tab" width="22" height="26" viewBox="0 0 22 26">
      <polygon points="0,0 14,0 22,13 14,26 0,26" fill="#3b3b3d"/>
      <polygon points="0,3 12,3 18,13 12,23 0,23" fill="none" stroke="#ffffff" stroke-width="1.5"/>
    </svg>

    <div class="identity">
      <div class="name">YOUR NAME</div>
      <div class="role">Manager</div>
    </div>

    <ul class="contacts">
      <li>
        <svg class="icon" viewBox="0 0 24 24" aria-hidden="true">
          <circle cx="12" cy="12" r="12" fill="#9b1d5a"/>
          <rect x="8.5" y="5.5" width="7" height="13" rx="1.2" fill="none" stroke="#fff" stroke-width="1.4"/>
          <line x1="11" y1="16" x2="13" y2="16" stroke="#fff" stroke-width="1.2"/>
        </svg>
        000-0000-000
      </li>
      <li>
        <svg class="icon" viewBox="0 0 24 24" aria-hidden="true">
          <circle cx="12" cy="12" r="12" fill="#9b1d5a"/>
          <rect x="6" y="8" width="12" height="8.5" fill="none" stroke="#fff" stroke-width="1.4"/>
          <polyline points="6,8 12,13 18,8" fill="none" stroke="#fff" stroke-width="1.4"/>
        </svg>
        www.lanternfold@gmail.com
      </li>
      <li>
        <svg class="icon" viewBox="0 0 24 24" aria-hidden="true">
          <circle cx="12" cy="12" r="12" fill="#9b1d5a"/>
          <path d="M12 19 C8.5 14.5 7.5 12.5 7.5 10.5 A4.5 4.5 0 0 1 16.5 10.5 C16.5 12.5 15.5 14.5 12 19 Z" fill="none" stroke="#fff" stroke-width="1.4"/>
          <circle cx="12" cy="10.5" r="1.6" fill="#fff"/>
        </svg>
        Your Address
      </li>
    </ul>

    <div class="brand">
      <div class="brand-square"></div>
      <div class="brand-name">Lanternfold</div>
    </div>

    <div class="band">
      <span class="web">www.lanternfold.com</span>
    </div>
  </section>

</main>
</body>
</html>
```